Mobile Fitness snd Therapy Business Card Design

I need a business card designed for my mobile fitness and therapy business.

Please view the images that I have uploaded. I like the simplicity of the design that I have attached. I adapted it with my information

Target Market(s)

Those seeking personal training, injury rehabilitation or massage therapy.

Industry/Entity Type

Business

Contact Information for Business Card

Derek Fulham - MSc, CAT(C), RMT, CSCS, Pn2
e-mail: derek@vantrelo.com
website: www.vantrelo.com
instagram: @derek_fulham

Font styles to use
Sans Serif

Colors
3176b5
0355a3

Requirements
Must have
• "Contact us to receive a FREE assessment"
• Services offered:
• Personal Training
• Golf Fitness
• Injury Rehab
• Massage Therapy
• Yoga
Nice to have
• Consistent colours with brand
• - Dark Blue: #232837
• - Blue: #5096f0
• Consistent look/feel with the website: www.vantrelo.com

```html
<!DOCTYPE html>
<html lang="en">
<head>
<meta charset="utf-8">
<title>Vantrelo Business Card</title>
<link href="https://fonts.googleapis.com/css2?family=Roboto+Condensed:wght@400;700&display=swap" rel="stylesheet">
<style>
  :root {
    --page: #e6e6e6;
    --card-light: #f4f4f4;
    --card-dark: #232837;
    --ink: #232837;
    --text-grey: #4a4a4a;
    --blue-deep: #2a5bd7;
    --blue-mid: #5096f0;
    --blue-soft: #8fbcf5;
    --rule: #b9b9b9;
    --white: #ffffff;
  }
  * { margin: 0; padding: 0; box-sizing: border-box; }
  html, body {
    width: 1200px; height: 960px; overflow: hidden;
    background: var(--page);
    font-family: "Roboto Condensed", Arial, sans-serif;
  }
  .canvas { position: relative; width: 1200px; height: 960px; }

  .card { position: absolute; width: 600px; height: 343px; overflow: hidden; }
  .card-front { left: 314px; top: 113px; background: var(--card-light); }
  .card-back { left: 311px; top: 472px; background: var(--card-dark); }

  .brand { position: absolute; text-align: center; }
  .brand-name { font-weight: 700; letter-spacing: 3px; line-height: 1; display: block; }
  .brand-tagline { font-weight: 700; letter-spacing: 2px; display: block; }

  .card-front .brand { left: 62px; top: 138px; width: 232px; }
  .card-front .brand-name { font-size: 34px; color: var(--ink); }
  .card-front .brand-tagline { font-size: 11.5px; color: var(--ink); margin-top: 5px; }

  .divider { position: absolute; left: 322px; top: 100px; width: 1px; height: 120px; background: var(--rule); }

  .contact { position: absolute; left: 351px; top: 100px; }
  .contact-name { font-size: 22px; font-weight: 700; color: var(--blue-deep); line-height: 1; }
  .contact-credentials { font-size: 11px; font-weight: 700; color: var(--blue-deep); margin-top: 4px; }
  .contact-list { list-style: none; margin-top: 19px; }
  .contact-list li { display: flex; align-items: center; font-size: 14.5px; color: var(--text-grey); height: 19.5px; }
  .contact-list svg { width: 13px; height: 13px; margin-right: 9px; flex: none; }

  .steps { position: absolute; left: 0; bottom: 0; width: 600px; height: 70px; }

  .card-back .brand { left: 0; top: 122px; width: 600px; }
  .card-back .brand-name { font-size: 50px; color: var(--white); letter-spacing: 5px; }
  .card-back .brand-tagline { font-size: 16px; color: var(--white); margin-top: 8px; letter-spacing: 2.5px; }

  .offer { position: absolute; left: 0; top: 266px; width: 600px; text-align: center; color: var(--white); }
  .offer-headline { font-size: 20.5px; font-weight: 700; }
  .offer-services { font-size: 14.5px; margin-top: 4px; }
  .offer-services .sep { color: var(--blue-mid); margin: 0 3px; }
</style>
</head>
<body>
<div class="canvas">

  <section class="card card-front">
    <div class="brand">
      <span class="brand-name">VANTRELO</span>
      <span class="brand-tagline">NUTRITION - FITNESS - HEALTH</span>
    </div>
    <div class="divider"></div>
    <div class="contact">
      <div class="contact-name">DEREK FULHAM</div>
      <div class="contact-credentials">MSC, CAT(C), RMT, CSCS, PN2</div>
      <ul class="contact-list">
        <li>
          <svg viewBox="0 0 13 13"><rect x="1" y="3" width="11" height="8" rx="1" fill="var(--blue-deep)"/><path d="M1.5 3.5 L6.5 7.5 L11.5 3.5" fill="none" stroke="var(--white)" stroke-width="1"/></svg>
          derek@vantrelo.com
        </li>
        <li>
          <svg viewBox="0 0 13 13"><circle cx="6.5" cy="6.5" r="5.5" fill="var(--blue-deep)"/><ellipse cx="6.5" cy="6.5" rx="2.3" ry="5.5" fill="none" stroke="var(--white)" stroke-width="0.9"/><line x1="1" y1="6.5" x2="12" y2="6.5" stroke="var(--white)" stroke-width="0.9"/></svg>
          www.vantrelo.com
        </li>
        <li>
          <svg viewBox="0 0 13 13"><circle cx="6.5" cy="6.5" r="6" fill="var(--blue-deep)"/><circle cx="6.5" cy="6.5" r="2" fill="none" stroke="var(--white)" stroke-width="1.1"/></svg>
          @derek_fulham
        </li>
      </ul>
    </div>
    <svg class="steps" viewBox="0 0 600 70" aria-hidden="true">
      <path d="M0 70 L186 50 Q196 49 196 60 L196 70 Z" fill="var(--blue-soft)"/>
      <path d="M201 70 L201 58 Q201 47 212 46 L386 28 Q398 27 398 40 L398 70 Z" fill="var(--blue-mid)"/>
      <path d="M404 70 L404 36 Q404 26 415 25 L584 7 Q600 5 600 22 L600 70 Z" fill="var(--blue-deep)"/>
    </svg>
  </section>

  <section class="card card-back">
    <div class="brand">
      <span class="brand-name">VANTRELO</span>
      <span class="brand-tagline">NUTRITION - FITNESS - HEALTH</span>
    </div>
    <div class="offer">
      <div class="offer-headline">CONTACT US TO RECEIVE A FREE ASSESSMENT</div>
      <div class="offer-services">Personal Training<span class="sep">|</span>Golf Fitness<span class="sep">|</span>Injury Rehab<span class="sep">|</span>Massage Therapy<span class="sep">|</span>Yoga</div>
    </div>
  </section>

</div>
</body>
</html>
```